Etiketten für Honig
Wir können nur volle Punktzahl geben. Roswitha ist selbst Ideenreich, wirklich nett und setzte unsere Ideen schnell und engagiert um. Hat echt Spass gemacht mit ihr zu arbeiten.
Zielgruppe
Es scheint Missverständnisse zu geben weshalb ich das Briefing wohl ändern muss.
see below for English translation
Wir sind eine kleine Imkerei, die von der Liebhaberei in den Nebenerwerb wechselt. Wir verkaufen verschiedene Sortenhonige und Honigzubereitungen (siehe Webseite) im vorwiegend ländlichen Raum des Münsterlandes.
Entsprechend unseres Standortes und unserer Kundschaft benötigen wir ein klassisch ländliches Design. Hierfür haben wir auch bereits ein Logo welches verwendet werden muss.
English
There seems to be some misunderstanding, so I guess I'll have to change the briefing.
We are a small apiary that changes from hobby to sideline. We sell different types of honey and honey preparations (e.g. honey with raspberry) in a predominantly rural area of the Münsterland (Muensterland).
According to our location and our clientele, we need a classic rural design. We already have a logo which must be used.
Aufgabenstellung
Wir möchten ein rechteckiges Etikett mit Gewährverschluss das für verschiedene Sorten adoptierbar ist. Zum Beispiel durch den Austausch der Sortenbezeichnung und eine farbliche Veränderung.
Das Design soll später auf Naturpapier oder Graspapier gedruckt werden. Das Logo muss auf Etikett und Gewährverschluss abgebildet werden.
We would like a rectangular label with a guarantee seal that is adoptable for different varieties. For example, by exchanging the variety designation and changing the color.
The design will later be printed on uncoated paper or grass paper. The logo must be shown on the label and guarantee seal.

```html
<!DOCTYPE html>
<html lang="de">
<head>
<meta charset="utf-8">
<title>Blütenhonig Etikett mit Gewährverschluss</title>
<link href="https://fonts.googleapis.com/css2?family=Caveat:wght@500;700&family=Caveat+Brush&family=Montserrat:wght@500;600&display=swap" rel="stylesheet">
<style>
  :root {
    --bg: #ececec;
    --label-pink: #d885bd;
    --pink-dark: #c8559f;
    --pink-soft: #e3a5cf;
    --honey-yellow: #f6c536;
    --white: #ffffff;
    --ink-soft: #555555;
  }
  html, body {
    margin: 0;
    padding: 0;
    width: 1200px;
    height: 960px;
    overflow: hidden;
    background: var(--bg);
  }
  .artboard {
    position: relative;
    width: 1200px;
    height: 960px;
  }
  /* guarantee seal */
  .seal-disc {
    position: absolute;
    left: 470px;
    top: 40px;
    width: 260px;
    height: 260px;
    border-radius: 50%;
    background: var(--label-pink);
    display: flex;
    align-items: center;
    justify-content: center;
    z-index: 2;
  }
  .seal-face {
    width: 206px;
    height: 206px;
    border-radius: 50%;
    background: var(--white);
    display: flex;
    flex-direction: column;
    align-items: center;
    justify-content: center;
    gap: 10px;
  }
  .brand-dot {
    width: 26px;
    height: 26px;
    border-radius: 50%;
    background: var(--honey-yellow);
  }
  .brand-name {
    font-family: "Caveat", cursive;
    font-weight: 700;
    font-size: 40px;
    color: var(--pink-dark);
    line-height: 1;
  }
  .seal-strip {
    position: absolute;
    left: 555px;
    top: 280px;
    width: 90px;
    height: 180px;
    background: var(--label-pink);
  }
  /* main label */
  .label {
    position: absolute;
    left: 90px;
    top: 455px;
    width: 1020px;
    height: 420px;
    background: var(--label-pink);
    overflow: hidden;
  }
  .bee-decoration {
    position: absolute;
    right: 0;
    top: 120px;
    width: 330px;
    height: 300px;
    z-index: 0;
    background: radial-gradient(ellipse at 60% 55%, var(--pink-soft) 0%, rgba(227,165,207,0.35) 55%, rgba(216,133,189,0) 75%);
  }
  .label-brand,
  .address,
  .product-note,
  .best-before,
  .producer-line,
  .variety,
  .claim,
  .weight-badge {
    z-index: 1;
  }
  .label-brand {
    position: absolute;
    left: 34px;
    top: 24px;
    font-family: "Caveat", cursive;
    font-weight: 700;
    font-size: 34px;
    color: var(--honey-yellow);
    line-height: 1;
  }
  .address {
    position: absolute;
    left: 34px;
    top: 70px;
    font-family: "Caveat", cursive;
    font-weight: 500;
    font-size: 19px;
    line-height: 1.15;
    color: var(--honey-yellow);
    margin: 0;
  }
  .product-note {
    position: absolute;
    left: 34px;
    top: 190px;
    font-family: "Caveat", cursive;
    font-weight: 500;
    font-size: 19px;
    line-height: 1.15;
    color: var(--honey-yellow);
    margin: 0;
  }
  .best-before {
    position: absolute;
    left: 34px;
    top: 300px;
    width: 200px;
    height: 60px;
    background: var(--white);
    font-family: "Montserrat", sans-serif;
    font-size: 10px;
    font-weight: 500;
    color: var(--ink-soft);
    padding: 5px 8px;
    box-sizing: border-box;
  }
  .producer-line {
    position: absolute;
    left: 430px;
    top: 34px;
    font-family: "Montserrat", sans-serif;
    font-weight: 500;
    font-size: 25px;
    letter-spacing: 1px;
    color: var(--honey-yellow);
    text-transform: uppercase;
  }
  .variety {
    position: absolute;
    left: 420px;
    top: 62px;
    margin: 0;
    font-family: "Caveat Brush", cursive;
    font-weight: 400;
    line-height: 0.82;
  }
  .variety-name {
    display: block;
    font-size: 150px;
    color: var(--white);
  }
  .variety-kind {
    display: block;
    font-size: 120px;
    color: var(--honey-yellow);
    margin-left: 100px;
  }
  .claim {
    position: absolute;
    left: 500px;
    top: 312px;
    margin: 0;
    font-family: "Caveat", cursive;
    font-weight: 700;
    font-size: 26px;
    line-height: 1.05;
    color: var(--honey-yellow);
  }
  .weight-badge {
    position: absolute;
    left: 760px;
    top: 292px;
    width: 86px;
    height: 86px;
  }
</style>
</head>
<body>
<main class="artboard">
  <div class="seal-disc">
    <div class="seal-face">
      <span class="brand-dot"></span>
      <span class="brand-name">Hollerbach</span>
    </div>
  </div>
  <div class="seal-strip"></div>

  <section class="label">
    <div class="bee-decoration" role="img" aria-label="Zarte Illustration einer Biene über Honigwaben"></div>
    <div class="label-brand">Hollerbach</div>
    <p class="address">Imkerei Hollerbach<br>Am Heidweg 7<br>49999 Heidekamp<br>Tel. 01234 567890</p>
    <p class="product-note">Honig aus der Region,<br>sorgsam geerntet und<br>schonend abgefüllt.</p>
    <div class="best-before">Mindestens haltbar bis:</div>

    <div class="producer-line">Hollerbacher Landhonig</div>
    <h1 class="variety">
      <span class="variety-name">Blüten</span>
      <span class="variety-kind">honig</span>
    </h1>
    <p class="claim">Echter Honig aus<br>dem Münsterland</p>
    <svg class="weight-badge" viewBox="0 0 86 86" aria-label="500 g">
      <polygon points="43,4 78,24 78,62 43,82 8,62 8,24" fill="var(--honey-yellow)"/>
      <text x="43" y="52" text-anchor="middle" font-family="Caveat, cursive" font-weight="700" font-size="28" fill="var(--white)">500 g</text>
    </svg>
  </section>
</main>
</body>
</html>
```